Veldmark Supplies Business Card

Professional business card that stand out to our potential customers. Front and back with clean modern design

Industry/Entity Type

Oil and gas

Contact Information for Business Card

Name, address, website , office phone and cell number

Requirements
Must have
• Editable files for each employee

```html
<!DOCTYPE html>
<html lang="en">
<head>
<meta charset="utf-8">
<title>Veldmark Supplies Business Card</title>
<link href="https://fonts.googleapis.com/css2?family=Mulish:wght@400;500;800&display=swap" rel="stylesheet">
<style>
  :root {
    --stage: #e9e9eb;
    --card: #ffffff;
    --brand-red: #e8202a;
    --brand-blue: #1aa7d0;
    --ink: #1c1c1c;
    --pattern-tone: #f1f1f1;
  }
  * { box-sizing: border-box; margin: 0; padding: 0; }
  html, body {
    width: 1200px; height: 1108px; overflow: hidden;
    background: var(--stage);
    font-family: "Mulish", sans-serif;
    color: var(--ink);
  }
  .card {
    position: absolute;
    background: var(--card);
    left: 218px; width: 776px;
  }
  .card-front { top: 50px; height: 472px; }
  .card-back { top: 568px; height: 456px; overflow: hidden; }

  .front-brand {
    position: absolute; left: 108px; top: 300px; width: 258px;
    display: flex; align-items: center; gap: 8px;
    white-space: nowrap;
  }
  .brand-square { width: 18px; height: 18px; background: var(--brand-red); flex: none; }
  .brand-name {
    font-weight: 800; font-size: 18px; color: var(--brand-red);
    letter-spacing: 0.3px; text-transform: uppercase;
  }
  .divider {
    position: absolute; left: 380px; top: 142px;
    width: 2px; height: 193px; background: var(--brand-red);
  }
  .contact-block { position: absolute; left: 400px; top: 138px; }
  .person-name { font-size: 30px; font-weight: 800; color: var(--brand-red); line-height: 1.1; }
  .person-role { font-size: 18px; font-weight: 400; margin-top: 4px; }
  .contact-list { list-style: none; margin-top: 20px; }
  .contact-list li {
    display: flex; align-items: center; gap: 8px;
    font-size: 18px; height: 30px;
  }
  .contact-list svg { width: 16px; height: 16px; fill: var(--brand-blue); flex: none; }
  .address {
    position: absolute; left: 0; right: 0; top: 395px;
    text-align: center; font-size: 18px;
  }

  .back-pattern { position: absolute; inset: 0; background: var(--pattern-tone); }
  .back-brand {
    position: absolute; left: 0; right: 0; top: 340px;
    display: flex; justify-content: center; align-items: center; gap: 16px;
    white-space: nowrap;
  }
  .back-brand .brand-square { width: 40px; height: 40px; }
  .back-brand .brand-name { font-size: 40px; }
</style>
</head>
<body>
  <section class="card card-front">
    <div class="front-brand">
      <span class="brand-square"></span>
      <span class="brand-name">Veldmark Supplies</span>
    </div>
    <div class="divider"></div>
    <div class="contact-block">
      <h1 class="person-name">Tarek Hollins</h1>
      <p class="person-role">President</p>
      <ul class="contact-list">
        <li>
          <svg viewBox="0 0 16 16" aria-hidden="true"><path d="M1 5c0-2 3-3 7-3s7 1 7 3v1h-3V5H4v1H1zM3 7h10l1 7H2zM8 9a2 2 0 1 0 0 4a2 2 0 0 0 0-4z"/></svg>
          +1.555.010.0400 x123
        </li>
        <li>
          <svg viewBox="0 0 16 16" aria-hidden="true"><path d="M3 1l3 3-2 2c1 2 3 4 5 5l2-2 3 3-2 3C6 14 2 10 1 3z"/></svg>
          +1.555.014.228
        </li>
        <li>
          <svg viewBox="0 0 16 16" aria-hidden="true"><path d="M1 3h14v1L8 9 1 4zM1 6l7 5 7-5v7H1z"/></svg>
          info@veldmarksupply.com
        </li>
        <li>
          <svg viewBox="0 0 16 16" aria-hidden="true"><circle cx="8" cy="8" r="7"/></svg>
          www.veldmarksupply.com
        </li>
      </ul>
    </div>
    <p class="address">48 Ridgeline Park Avenue Dover, NJ 07801 USA</p>
  </section>

  <section class="card card-back">
    <div class="back-pattern" role="img" aria-label="Faint repeating brand pattern in light grey"></div>
    <div class="back-brand">
      <span class="brand-square"></span>
      <span class="brand-name">Veldmark Supplies</span>
    </div>
  </section>
</body>
</html>
```